New Template, new corporate image Kelvoran 2022

New template designs for google slides or PowerPoint. Match to new corporate image. The new website www.kelvoran-mx.example Needs to match our new version. Technology and Artificial Intelligence elements to reflect our type of work.
We are adding old version of template and will send elements for the new corporate images.
Please consider our website as the main corporate image.
Our templates are being used on customer presentations, webminars, internal work only.
We have our main name of company Kelvoran. Kelvoran has to be in all the templates.
Secondary logo or branded service is: Vastrelim.

Target Market(s)

Industrial users. Asset managers. Corporate visitors and customers.

Industry/Entity Type

Automotive. Chemical. Food and Beverage. Manufacturing

Other font styles liked:
• GE INSPIRA. RALEWAY

Colors
0054AA
0677BA
7BADD7
CADEEF
E8F1F8

Requirements
Must have
• Match to our elements on the new image. Use Brain Icons. Chips icons to connect equipments with software and control. Innovation.
Nice to have
• Unique images, machine images. Connecting machines and data elements. Template version for google slides. Image for industrial software for control equipment and saving money to manufacturers. Segments: Automotive, Chemical, Food and Beverages, Mining and pharmaceutical, Energy Management
Should not have
• old elements. not to much images of medical devices. Do not seems like a hospital.

```html
<!DOCTYPE html>
<html lang="en">
<head>
<meta charset="utf-8">
<title>Kelvoran Presentation Template 2022</title>
<link rel="stylesheet" href="https://fonts.googleapis.com/css2?family=Montserrat:wght@400;500;600;700&family=Open+Sans:wght@400;600&display=swap">
<style>
:root{
  --page:#f2f3f5;
  --white:#ffffff;
  --navy:#0c2b45;
  --navy-deep:#07192b;
  --ink:#1b3850;
  --blue:#1a5585;
  --steel:#7fa6b8;
  --steel-light:#8fb1c2;
  --grey:#b5b8ba;
  --text:#55606a;
  --line:#dfe3e7;
  --cyan:#5db8d8;
}
*{box-sizing:border-box;margin:0;padding:0}
html,body{width:1200px;height:4208px;overflow:hidden}
body{background:var(--page);position:relative;font-family:"Open Sans",Arial,sans-serif;color:var(--text)}
.slide{position:absolute;left:51px;width:1098px;height:619px;overflow:hidden;background:var(--white);box-shadow:0 2px 8px rgba(0,0,0,.08)}
.s1{top:70px}.s2{top:769px}.s3{top:1455px}.s4{top:2138px}.s5{top:2837px}.s6{top:3514px}
.wordmark{font-family:"Montserrat",sans-serif;font-weight:600;letter-spacing:.5px}
.title-block{position:absolute;left:34px;top:22px}
.title-block .dash{width:40px;height:2px;background:var(--ink);margin-bottom:14px}
.title-block h2{font-family:"Montserrat",sans-serif;font-weight:500;font-size:25px;color:var(--ink);line-height:1}
.title-block p{font-family:"Montserrat",sans-serif;font-size:11px;color:var(--text);margin-top:6px;letter-spacing:.3px}
.dark .title-block .dash{background:#fff}
.dark .title-block h2,.dark .title-block p{color:#fff}
.footer{position:absolute;left:0;right:0;bottom:0;height:40px}
.footer .wordmark{position:absolute;left:26px;top:10px;font-size:17px;color:var(--blue)}
.footer .copy{position:absolute;left:0;right:0;top:14px;text-align:center;font-size:11px;color:#333}
.footer .page{position:absolute;right:10px;top:16px;font-size:10px;color:#333}
.dark .footer .wordmark,.dark .footer .copy,.dark .footer .page{color:#fff}
.corner{position:absolute;right:0;top:0}

.cover-art{position:absolute;inset:0;background:radial-gradient(circle at 73% 40%,#bff3f5 0,#6fd0d8 14%,#1d6e93 30%,#0f4a74 55%,#0a3356 100%)}
.s1 .wordmark{position:absolute;left:52px;top:262px;font-size:72px;color:#fff}

.services-line{position:absolute;left:57px;right:51px;top:206px;border-top:2px dotted #8a96a0}
.service{position:absolute;width:146px;top:182px}
.service .icon{width:50px;height:50px;margin:0 auto;border-radius:50%;background:#fff;box-shadow:0 2px 8px rgba(0,0,0,.15);display:flex;align-items:center;justify-content:center}
.service .card{margin-top:20px;height:236px;border:1px solid var(--line);border-radius:4px;background:#fff;padding:20px 10px 0;text-align:center}
.service h3{font-family:"Montserrat",sans-serif;font-size:13.5px;font-weight:700;color:#111;line-height:1.25;min-height:34px;display:flex;align-items:flex-start;justify-content:center}
.service p{font-size:9.2px;line-height:1.85;color:#666}

.s3{background:linear-gradient(90deg,#0a1f38 0,#050d1b 60%,#03080f 100%)}
.hand-art{position:absolute;left:0;top:100px;width:500px;height:519px;background:radial-gradient(ellipse at 50% 35%,#6c86e6 0,#2a4ea8 22%,#0d2a55 50%,rgba(5,13,27,0) 75%)}
.feature{position:absolute;left:491px;width:573px;height:116px;border:1px solid rgba(255,255,255,.35);display:flex}
.feature .icon{width:121px;flex:none;display:flex;align-items:center;justify-content:center;border-right:1px solid rgba(255,255,255,.3);margin:14px 0}
.feature .body{padding:18px 16px 0 32px}
.feature h3{font-family:"Montserrat",sans-serif;font-weight:500;font-size:19px;color:var(--cyan);letter-spacing:.5px}
.feature p{font-size:12px;line-height:1.9;color:#e6edf3;margin-top:8px;text-align:justify}

.s4 h1{position:absolute;left:94px;top:160px;width:480px;font-family:"Montserrat",sans-serif;font-weight:700;font-size:38px;line-height:1.37;color:var(--ink)}
.s4 h1 em{font-style:normal;color:var(--steel)}
.s4 .copy-text{position:absolute;left:96px;width:470px;font-size:9.5px;line-height:2.15;color:#555;text-align:justify}
.robot-art{position:absolute;left:648px;top:121px;width:338px;height:403px;border-radius:14px;background:linear-gradient(160deg,#e6eef0 0,#c8dadd 45%,#9fb8bd 100%);box-shadow:0 6px 16px rgba(0,0,0,.25);border:4px solid #fff}

.donut{position:absolute;left:68px;top:131px}
.note{position:absolute;left:512px;width:550px;height:98px;border-left:3px solid var(--ink);padding:14px 0 0 30px;background:linear-gradient(90deg,#f3f5f7,#fff)}
.note p{font-size:9.5px;line-height:2.3;color:#555}

.s6{background:var(--navy)}
.closing-art{position:absolute;inset:0;background:linear-gradient(135deg,#0e3a63 0,#0c3358 50%,#123e66 75%,#0a2c4c 100%)}
.s6 .wordmark{position:absolute;left:90px;top:262px;font-size:76px;color:#fff}
.s6 .divider{position:absolute;left:621px;top:165px;width:2px;height:284px;background:#fff}
.s6 h2{position:absolute;left:709px;top:160px;font-family:"Montserrat",sans-serif;font-weight:400;font-size:46px;color:#fff}
.contacts{position:absolute;left:712px;top:250px;list-style:none}
.contacts li{display:flex;align-items:flex-start;gap:16px;color:#fff;font-size:17px;line-height:1.3;margin-bottom:22px;width:300px}
.contacts svg{flex:none;margin-top:3px}
</style>
</head>
<body>

<section class="slide s1">
  <div class="cover-art" role="img" aria-label="Blue cave opening with a glowing tree shaped like a head over misty hills"></div>
  <div class="wordmark">Kelvoran</div>
</section>

<section class="slide s2">
  <svg class="corner" width="122" height="122" viewBox="0 0 122 122"><polygon points="0,0 122,0 122,122" fill="var(--steel-light)"/></svg>
  <div class="title-block"><div class="dash"></div><h2>YOUR TITLE HERE</h2><p>SUBTITLE GOES HERE</p></div>
  <div class="services-line"></div>

  <div class="service" style="left:54px">
    <div class="icon"><svg width="26" height="26" viewBox="0 0 24 24" fill="none" stroke="#222" stroke-width="1.6"><path d="M4 14v-2a8 8 0 0116 0v2"/><rect x="3" y="13" width="4" height="6" rx="1.5"/><rect x="17" y="13" width="4" height="6" rx="1.5"/></svg></div>
    <div class="card"><h3>TECH SUPPORT</h3><p>We provide solutions to any event, we have a team experts in industrial auto mation.We provide to any event, we have a team of experts in industrial auto mation.We provide to any event, we have a team of industrial automation.</p></div>
  </div>
  <div class="service" style="left:223px">
    <div class="icon"><svg width="26" height="26" viewBox="0 0 24 24" fill="none" stroke="#222" stroke-width="1.6"><path d="M2 9l10-5 10 5-10 5z"/><path d="M6 11v5c3 2 9 2 12 0v-5"/><path d="M22 9v5"/></svg></div>
    <div class="card"><h3>CERTIFICATION</h3><p>We offer official certifica-tions based on the need of our customers.We provide solutions to any event, we have a team experts in industrial auto mation.We provide to any event, we have a team of experts in industrial auto mation.</p></div>
  </div>
  <div class="service" style="left:392px">
    <div class="icon"><svg width="26" height="26" viewBox="0 0 24 24" fill="none" stroke="#222" stroke-width="1.6"><rect x="3" y="4" width="18" height="12" rx="1.5"/><path d="M8 20h8M12 16v4M3 13h18"/></svg></div>
    <div class="card"><h3>TECH COURSES</h3><p>We offer completely custo mized courses based on the need of our customers. We provide solutions to any event, we have a team experts in industrial auto mation.We provide to any event, we have a team of industrial auto mation.</p></div>
  </div>
  <div class="service" style="left:562px">
    <div class="icon"><svg width="26" height="26" viewBox="0 0 24 24" fill="none" stroke="#222" stroke-width="1.6"><path d="M6 3h8l4 4v14H6z"/><path d="M14 3v4h4M9 12h6M9 16h6"/></svg></div>
    <div class="card"><h3>DIAGNOSTICS</h3><p>We provide solutions to any event, we have a team experts in industrial auto mation.We provide to any event, we have a team of experts in industrial auto mation.We provide to any event, we have a team of industrial automation.</p></div>
  </div>
  <div class="service" style="left:731px">
    <div class="icon"><svg width="26" height="26" viewBox="0 0 24 24" fill="none" stroke="#222" stroke-width="1.6"><circle cx="12" cy="12" r="9"/><path d="M3 12h18M12 3c3 3 3 15 0 18M12 3c-3 3-3 15 0 18"/></svg></div>
    <div class="card"><h3>CONSULTORY</h3><p>We provide solutions to any event, we have a team experts in industrial auto mation.We provide to any event, we have a team of experts in industrial auto mation.We provide to any event, we have a team of industrial automation.</p></div>
  </div>
  <div class="service" style="left:901px">
    <div class="icon"><svg width="28" height="26" viewBox="0 0 26 24" fill="none" stroke="#222" stroke-width="1.6"><path d="M2 8l4-3 5 2 4-2 5 1 4 3-3 5-8 6-4-3-5-4z"/><path d="M11 7l-3 4 3 1 4-3 5 4"/></svg></div>
    <div class="card"><h3>CUSTOMER ATTENTION</h3><p>We provide solutions to any event, we have a team experts in industrial auto mation.We provide to any event, we have a team of experts in industrial auto mation.We provide to any event, we have a team of industrial automation.</p></div>
  </div>

  <div class="footer"><span class="wordmark">Kelvoran</span><span class="copy">© Copyright 2022 Kelvoran.All Rights Reserved.</span><span class="page">Page 02</span></div>
</section>

<section class="slide s3 dark">
  <div class="hand-art" role="img" aria-label="Hand holding a smartphone with a glowing cloud upload symbol above a city skyline"></div>
  <div class="title-block"><div class="dash"></div><h2>YOUR TITLE HERE</h2><p>SUBTITLE GOES HERE</p></div>

  <div class="feature" style="top:111px">
    <div class="icon"><svg width="64" height="64" viewBox="0 0 64 64" fill="none" stroke="#fff" stroke-width="1.6"><rect x="14" y="52" width="24" height="6"/><path d="M26 52V34l12-14 10 4"/><circle cx="26" cy="34" r="3"/><circle cx="38" cy="20" r="3"/><path d="M48 24v8m-4 0h8"/></svg></div>
    <div class="body"><h3>SMART MACHINES</h3><p>Intelligent machines in operation and control, in the same synchronization regardless of the brand installed.</p></div>
  </div>
  <div class="feature" style="top:243px">
    <div class="icon"><svg width="64" height="64" viewBox="0 0 64 64" fill="none" stroke="#fff" stroke-width="1.6"><circle cx="32" cy="32" r="9"/><circle cx="32" cy="32" r="17"/><path d="M32 8v7M32 49v7M8 32h7M49 32h7M15 15l5 5M44 44l5 5M15 49l5-5M44 20l5-5"/></svg></div>
    <div class="body"><h3>OPERATIONAL EXCELLENCE</h3><p>Operational excellence is part of our language, strengthening the efficiency in the company delivers revolutionary results.</p></div>
  </div>
  <div class="feature" style="top:375px">
    <div class="icon"><svg width="64" height="64" viewBox="0 0 64 64" fill="none" stroke="#fff" stroke-width="1.6"><path d="M8 56V34l10 6v-6l10 6v-6l10 6V14h6v-4h4v4h4v42z"/><path d="M6 56h52M20 48h4M30 48h4M40 48h4"/></svg></div>
    <div class="body"><h3>INDUSTRIAL INTERNET</h3><p>Extending the Internet to industrial operation will exceed global energy savings by more than 1 Billion USD.</p></div>
  </div>

  <div class="footer"><span class="wordmark">Kelvoran</span><span class="copy" style="text-align:left;left:414px">© Copyright 2022 Kelvoran.All Rights Reserved.</span><span class="page" style="right:30px">Page 03</span></div>
</section>

<section class="slide s4">
  <svg class="corner" width="122" height="138" viewBox="0 0 122 138"><polygon points="0,0 122,0 122,138" fill="var(--navy)"/></svg>
  <div class="title-block"><div class="dash"></div><h2>YOUR TITLE HERE</h2><p>SUBTITLE GOES HERE</p></div>
  <h1>Tessavor is one of the pillars of our <em>digital transformation</em> strategy</h1>
  <p class="copy-text" style="top:342px">From a sensor, a PLC, Pac system or any advanced control system, it can all be brought together using the powerful Tessavor interoperability software. The first step is not difficult, since the current existing infrastructure is the first thing you can connect, without the need to modify, change or spend additionally. Tessavor is a very flexible, open, multiprotocol tool and has the ability to connect any existing device.</p>
  <p class="copy-text" style="top:460px">You can request a 30-day demo license at no cost, we know it will be very useful, connect with an technical advisor, we can guide you to solve these new challenges in the new normal.</p>
  <div class="robot-art" role="img" aria-label="Hand holding a phone with orange industrial robot arms above it"></div>
  <div class="footer"><span class="wordmark">Kelvoran</span><span class="copy">© Copyright 2022 Kelvoran.All Rights Reserved.</span><span class="page">Page 04</span></div>
</section>

<section class="slide s5">
  <svg class="corner" width="122" height="138" viewBox="0 0 122 138"><polygon points="0,0 122,0 122,138" fill="var(--navy)"/></svg>
  <div class="title-block"><div class="dash"></div><h2>YOUR TITLE HERE</h2><p>SUBTITLE GOES HERE</p></div>
  <svg class="donut" width="360" height="380" viewBox="-180 -180 360 380">
    <ellipse cx="20" cy="182" rx="150" ry="10" fill="#000" opacity=".08"/>
    <path d="M0,-177 A177,177 0 0 1 168.3,54.7 L108.4,35.2 A114,114 0 0 0 0,-114 Z" fill="var(--blue)"/>
    <path d="M168.3,54.7 A177,177 0 0 1 104.1,143.2 L67,92.2 A114,114 0 0 0 108.4,35.2 Z" fill="var(--steel-light)"/>
    <path d="M104.1,143.2 A177,177 0 0 1 0,177 L0,114 A114,114 0 0 0 67,92.2 Z" fill="var(--grey)"/>
    <path d="M0,177 A177,177 0 0 1 0,-177 L0,-114 A114,114 0 0 0 0,114 Z" fill="var(--navy)"/>
    <g font-family="Montserrat,sans-serif" font-weight="700" font-size="13" fill="#fff" text-anchor="middle">
      <text x="132" y="-70">30%</text>
      <text x="150" y="73">10%</text>
      <text x="44" y="149">10%</text>
      <text x="-141" y="-18">50%</text>
    </g>
    <text x="0" y="8" text-anchor="middle" font-family="Montserrat,sans-serif" font-weight="600" font-size="27" fill="var(--blue)">Kelvoran</text>
  </svg>
  <div class="note" style="top:75px"><p>Sed ut perspiciatis unde omnis iste natus error sit voluptatem accusant ium doloremque laudantium, totam rem aperiam, eaque ipsa quae ab illo inventore veritatis et quasi architecto beatae vitae dicta sunt explicabo. nemo enim ipsam voluptatem quia</p></div>
  <div class="note" style="top:196px"><p>Sed ut perspiciatis unde omnis iste natus error sit voluptatem accusant ium doloremque laudantium, totam rem aperiam, eaque ipsa quae ab illo inventore veritatis et quasi architecto beatae vitae dicta sunt explicabo. nemo enim ipsam voluptatem quia</p></div>
  <div class="note" style="top:316px"><p>Sed ut perspiciatis unde omnis iste natus error sit voluptatem accusant ium doloremque laudantium, totam rem aperiam, eaque ipsa quae ab illo inventore veritatis et quasi architecto beatae vitae dicta sunt explicabo. nemo enim ipsam voluptatem quia</p></div>
  <div class="note" style="top:437px"><p>Sed ut perspiciatis unde omnis iste natus error sit voluptatem accusant ium doloremque laudantium, totam rem aperiam, eaque ipsa quae ab illo inventore veritatis et quasi architecto beatae vitae dicta sunt explicabo. nemo enim ipsam voluptatem quia</p></div>
  <div class="footer"><span class="wordmark">Kelvoran</span><span class="copy">© Copyright 2022 Kelvoran.All Rights Reserved.</span><span class="page">Page 04</span></div>
</section>

<section class="slide s6 dark">
  <div class="closing-art" role="img" aria-label="Deep blue photo of a hand using a tablet with faint technology graphics"></div>
  <div class="wordmark">Kelvoran</div>
  <div class="divider"></div>
  <h2>Thank You</h2>
  <ul class="contacts">
    <li><svg width="16" height="18" viewBox="0 0 24 24" fill="#fff"><path d="M12 2a7 7 0 00-7 7c0 5 7 13 7 13s7-8 7-13a7 7 0 00-7-7zm0 9.5A2.5 2.5 0 1112 6.5a2.5 2.5 0 010 5z"/></svg><span>Lorem ipsum dolor sit amet, consectetur</span></li>
    <li><svg width="16" height="18" viewBox="0 0 24 24" fill="#fff"><path d="M6.6 10.8a15 15 0 006.6 6.6l2.2-2.2a1 1 0 011-.25 11.4 11.4 0 003.6.6 1 1 0 011 1V20a1 1 0 01-1 1A17 17 0 013 4a1 1 0 011-1h3.5a1 1 0 011 1c0 1.25.2 2.45.6 3.6a1 1 0 01-.25 1z"/></svg><span>555-010-0188</span></li>
    <li><svg width="16" height="18" viewBox="0 0 24 24" fill="none" stroke="#fff" stroke-width="2"><circle cx="12" cy="12" r="9"/><path d="M3 12h18M12 3c3 3 3 15 0 18M12 3c-3 3-3 15 0 18"/></svg><span>www.yourwebsite.example</span></li>
    <li><svg width="16" height="18" viewBox="0 0 24 24" fill="#fff"><path d="M2 6a1 1 0 011-1h18a1 1 0 011 1v.5l-10 6-10-6zM2 8.8l10 6 10-6V18a1 1 0 01-1 1H3a1 1 0 01-1-1z"/></svg><span>companyname@mail.example</span></li>
  </ul>
  <div class="footer"><span class="copy" style="text-align:left;left:26px">© Copyright 2022 Kelvoran.All Rights Reserved.</span><span class="page">Page 06</span></div>
</section>

</body>
</html>
```